July 2022 Industrial Manufacturer Product Expo Mexico City

We manufacture large screws and fastners for large Mining equipment, Trains, large ships, airplanes, wind turbines, and so on. We also do custom work base on the customer needs. No matter the size we can make it.
We have a Expo coming up with companies all over the world. We have to stand out we are a family own business so our customer service will be above and beyond anyone can provide. We do not have a sales force to push our products and services we provide one on one service.
Plus@!! I'm looking for anything that you designers can come up with if it was your company to put on a business card, plus i want to do a 1 or 2 sided pamphlet, and then a website. We make Speciality Bolts for large mining equipment these bolts can be 3 to 4 foot long!!! Plus fasteners, Nuts, washers, any, size, strengths, special materials, we offer more of a ono on one customer service, We are a small company, family own, but can fulfill any type of orders. We can also provide special time lines for emergency orders. "We keep the machines running we here at KRV don't believe in down time" We want to hear any slogan based on our company to stand out.
Thanks i really appreciate all your work and options that we have to pick on. Plus just a thought we could possibly want to entertain a experience Marketing internet help maybe a employment possibility. Thanks

I need 2 cards one in Spanish and English Like the steel back ground maybe send me in some bright red and blue writing Same with the Black cards Please remove the word Military The logo KRV maybe integrate a picture of a Bolt 🔩 Thank you

Still looking for I need 2 cards one in Spanish and English Like the steel back ground maybe send me in some bright red and blue writing Same with the Black cards try bright writing Please remove the word Military The logo KRV maybe integrate a picture of a Bolt 🔩 Plus will need the company to make a brochure and website next Thank you

Target Market(s)

Large Mining, Ship, Train, Green Energy, VELM, and Government equipment. Throughout the World

Industry/Entity Type

We can Custom Manufacture any type of Fastners for Mining equipment, Trains, Ships, Green energy, Governments, or military projects. wind turbines,

Contact Information for Business Card

I attached the name and contact info that's on a card, plus the Company Logo. Would like industrial looking background with Bright Colors that will stand out!! If we can insert somewhere maybe on back that we "Custom Manufacture Any Size or Quantity Fastners for Large Mining Equipment, Trains, Ships, Green Energy Equipment or Government Projects

Font styles to use
Other font styles liked:
• You Pick, has to be bold, colorful standout, Professional looking Beable to read it.

Colors

Designer to choose colors to be used in the design.

Requirements
Must have
• Need in Spanish and English TO STANDOUT FROM THE REST OF THE EXPO!! See Business card details, Rounded corners
Nice to have
• Can i see some of the darker cards with Bright Red and Blue letters I like to see the different type of card material, heavy thickness, plastic, transparent, Metal types, Bright Colors, I saw like Raised letters like on the logo.

```html
<!DOCTYPE html>
<html lang="es">
<head>
<meta charset="utf-8">
<title>KRV – Tarjetas de presentación</title>
<link rel="stylesheet" href="https://fonts.googleapis.com/css2?family=Open+Sans:wght@400;600&display=swap">
<style>
  :root {
    --page-bg: #1e1e1f;
    --card-bg: #0b0b0b;
    --card-edge: #151515;
    --brand-blue: #1a8fd6;
    --accent-red: #e8242c;
    --text-white: #f2f2f2;
    --rule-grey: #2e2e2e;
  }
  * { box-sizing: border-box; margin: 0; padding: 0; }
  html, body {
    width: 1200px; height: 900px; overflow: hidden;
    background: var(--page-bg);
    font-family: "Open Sans", Arial, sans-serif;
  }
  .sheet {
    width: 1200px; height: 900px;
    display: flex; flex-direction: column;
    align-items: center; justify-content: center;
    gap: 56px;
  }
  .card {
    position: relative;
    width: 620px; height: 354px;
    background: var(--card-bg);
    border: 1px solid var(--card-edge);
    border-radius: 10px;
    overflow: hidden;
  }
  .brand-name {
    font-family: "Open Sans", Arial, sans-serif;
    font-weight: 600;
    color: var(--brand-blue);
    letter-spacing: 4px;
    line-height: 1;
  }
  .brand-dot {
    width: 12px; height: 12px; border-radius: 50%;
    background: var(--accent-red);
  }
  /* Front */
  .card-front .brand {
    position: absolute; left: 68px; top: 150px;
    display: flex; align-items: center; gap: 12px;
  }
  .card-front .brand-name { font-size: 46px; }
  .card-front .divider {
    position: absolute; left: 282px; top: 70px;
    width: 1px; height: 214px;
    background: var(--accent-red);
    opacity: 0.7;
  }
  .contact {
    position: absolute; left: 314px; top: 104px;
    color: var(--text-white);
  }
  .contact .person {
    color: var(--brand-blue);
    font-size: 20px; font-weight: 400;
    margin-bottom: 16px;
  }
  .contact .role, .contact .email {
    font-size: 16px; line-height: 1.35;
  }
  .contact .phones {
    display: flex; align-items: center; gap: 8px;
    margin-top: 12px; font-size: 17px;
  }
  .contact .phones svg { width: 16px; height: 16px; flex: none; }
  /* Back */
  .card-back .brand {
    position: absolute; left: 0; right: 0; top: 92px;
    display: flex; justify-content: center; align-items: center; gap: 14px;
  }
  .card-back .brand-name { font-size: 72px; }
  .card-back .brand-dot { width: 16px; height: 16px; }
  .tagline {
    position: absolute; left: 60px; right: 60px; top: 214px;
    color: var(--text-white);
    text-align: center;
    font-size: 15px; line-height: 1.4;
  }
  .tagline-rule {
    position: absolute; left: 270px; top: 196px;
    width: 80px; height: 2px;
    background: var(--accent-red);
  }
</style>
</head>
<body>
<main class="sheet">
  <section class="card card-front" aria-label="Frente de la tarjeta">
    <div class="brand">
      <span class="brand-name">KRV</span>
      <span class="brand-dot"></span>
    </div>
    <div class="divider"></div>
    <div class="contact">
      <p class="person">Lic.Marisol Ortega Vidal</p>
      <p class="role">Cotizaciones en</p>
      <p class="email">krvtornilleria.ventas@correo.mx</p>
      <p class="phones">
        <svg viewBox="0 0 24 24" aria-hidden="true"><path fill="var(--accent-red)" d="M6.6 10.8a15.1 15.1 0 0 0 6.6 6.6l2.2-2.2c.3-.3.7-.4 1-.2 1.1.4 2.3.6 3.6.6.6 0 1 .4 1 1V20c0 .6-.4 1-1 1A17 17 0 0 1 3 4c0-.6.4-1 1-1h3.5c.6 0 1 .4 1 1 0 1.3.2 2.5.6 3.6.1.3 0 .7-.2 1z"/></svg>
        <span>8714205518</span>
        <svg viewBox="0 0 24 24" aria-hidden="true"><rect x="6" y="2" width="12" height="20" rx="2" fill="none" stroke="var(--accent-red)" stroke-width="2"/><rect x="10" y="18" width="4" height="1.6" fill="var(--accent-red)"/></svg>
        <span>8719036274</span>
      </p>
    </div>
  </section>

  <section class="card card-back" aria-label="Reverso de la tarjeta">
    <div class="brand">
      <span class="brand-name">KRV</span>
      <span class="brand-dot"></span>
    </div>
    <div class="tagline-rule"></div>
    <p class="tagline">Custom Manufacture Any Size or Quantity Fastners for Large<br>Mining Equipment, Trains, Ships, Green Energy Equipment<br>or Government Projects</p>
  </section>
</main>
</body>
</html>
```